Quillmarsh Property Solutions need a business card design

Hello guys. We would need a business card design asap please.
We are a start up property investment business based in London UK specialised in buying, selling, managing and letting properties and helping distressed property owners.
The name of our Business is Quillmarsh, the logo symbolises the four fundamental elements of the world (earth, air, fire and water) and so it stands for strength, stability, longevity.
We would like the business card to communicate professionalism and reliability. Many many thanks indeed for your work.

Details:

1.) Rosalind Updike
Property Investor
Mobile: +44(0)7700123456
Email: rosalind.quillmarsh@mailbox-example.com

2.) Dominic Updike
Property Investor
Mobile: +44(0)7700987654
Email: dominic.quillmarsh@mailbox-example.com

```html
<!DOCTYPE html>
<html lang="en">
<head>
<meta charset="UTF-8">
<title>Quillmarsh Property Solutions – Business Card</title>
<link rel="stylesheet" href="https://fonts.googleapis.com/css2?family=League+Spartan:wght@700&family=Source+Sans+3:wght@400;600&display=swap">
<style>
  :root {
    --backdrop: #e9e6e1;
    --card: #ffffff;
    --ink: #111111;
    --ink-soft: #5a5a5a;
    --accent: #3f9a4a;
    --card-shadow: rgba(0, 0, 0, 0.18);
  }
  * { box-sizing: border-box; margin: 0; padding: 0; }
  html, body {
    width: 1200px;
    height: 720px;
    overflow: hidden;
    background: var(--backdrop);
  }
  .canvas {
    width: 1200px;
    height: 720px;
    display: flex;
    align-items: center;
    justify-content: center;
    gap: 48px;
  }
  .card {
    width: 540px;
    height: 309px;
    background: var(--card);
    box-shadow: 0 6px 18px var(--card-shadow);
    position: relative;
  }

  /* Front side */
  .card-front {
    display: flex;
    flex-direction: column;
    align-items: center;
    padding-top: 52px;
  }
  .brand {
    display: flex;
    flex-direction: column;
    align-items: center;
  }
  .brand-mark {
    width: 22px;
    height: 22px;
    background: var(--accent);
    margin-bottom: 12px;
  }
  .brand-name {
    font-family: "League Spartan", sans-serif;
    font-weight: 700;
    font-size: 26px;
    letter-spacing: 0.5px;
    color: var(--ink);
    line-height: 1;
  }
  .brand-tagline {
    font-family: "League Spartan", sans-serif;
    font-weight: 700;
    font-size: 9px;
    letter-spacing: 0.6px;
    color: var(--ink);
    margin-top: 4px;
  }
  .contact {
    margin-top: 40px;
    display: flex;
    flex-direction: column;
    align-items: center;
    font-family: "Source Sans 3", sans-serif;
    color: var(--ink-soft);
  }
  .person {
    font-size: 17px;
    margin-bottom: 8px;
  }
  .person-name {
    font-weight: 600;
    text-transform: uppercase;
    letter-spacing: 0.3px;
  }
  .contact-line {
    display: flex;
    align-items: center;
    gap: 7px;
    font-size: 15px;
    line-height: 1.5;
  }
  .contact-line svg {
    width: 12px;
    height: 12px;
    fill: var(--ink-soft);
  }

  /* Back side */
  .card-back {
    display: flex;
    flex-direction: column;
    align-items: center;
    justify-content: center;
  }
  .back-name {
    font-family: "League Spartan", sans-serif;
    font-weight: 700;
    font-size: 56px;
    letter-spacing: 1px;
    color: var(--ink);
    line-height: 1;
  }
  .back-tagline {
    font-family: "League Spartan", sans-serif;
    font-weight: 700;
    font-size: 22px;
    letter-spacing: 0.8px;
    color: var(--ink);
    margin-top: 10px;
  }
</style>
</head>
<body>
<main class="canvas">
  <section class="card card-front" aria-label="Business card front">
    <div class="brand">
      <span class="brand-mark"></span>
      <span class="brand-name">QUILLMARSH</span>
      <span class="brand-tagline">PROPERTY SOLUTIONS</span>
    </div>
    <div class="contact">
      <p class="person"><span class="person-name">Dominic Updike</span>, Property Investor</p>
      <p class="contact-line">
        <svg viewBox="0 0 12 12" aria-hidden="true"><path d="M3 0h6a1 1 0 0 1 1 1v10a1 1 0 0 1-1 1H3a1 1 0 0 1-1-1V1a1 1 0 0 1 1-1zm0.5 1.5v7h5v-7zM6 9.5a0.8 0.8 0 1 0 0 1.6a0.8 0.8 0 0 0 0-1.6z"/></svg>
        +44(0)7700987654
      </p>
      <p class="contact-line">
        <svg viewBox="0 0 12 12" aria-hidden="true"><path d="M0 2h12v8H0zm1 1v0.4l5 3.2l5-3.2V3zm0 1.6V9h10V4.6L6 7.8z"/></svg>
        dominic.quillmarsh@mailbox-example.com
      </p>
    </div>
  </section>

  <section class="card card-back" aria-label="Business card back">
    <h1 class="back-name">QUILLMARSH</h1>
    <p class="back-tagline">PROPERTY SOLUTIONS</p>
  </section>
</main>
</body>
</html>
```